Business Card Design for Vintage Jazz

I am a vintage jazz band leader in New York City. My groups play the music of the 1920s, 1930s and 1940s. My website is morvalquist.com for more info on what I do.

I am looking for a two sided business card design that has the look and feel of a really nice business card from the 1930s. I need to convey with the design that my work has that vintage kind of class and style, but also conveys that we are fun and entertaining.

Most importantly it should make a bold staement. If Hal Denbrook had a card, what would it have looked like? I want a card that I feel confident will make an impact and will let people know that my work is te the top that NYC has to offer in vintage jazz..

Note that I have only decided to avoid the "committed payment" option as I have not used this service before. Assuming that I get quality work I will select a design from those presented.

Target Market(s)

people who want to hire my band for events, media, and new fans of the band

Industry/Entity Type

Performing Art

Contact Information for Business Card

Definitely a matte finish, possibly a sort of old style of paper with that brown tint? definitely a thick card.

Requirements
Must have
• FRONT
• My name: Tobin Vashley
• What I do: Bandleader, Guitarist, Vocalist, Songwriter
• Contact Details: morvalquist.com tobin@morvalquist.com 646-555-0148
• BACK
• My Social Media Links:
• facebook.morvalquist.com
• twitter, instagram, linkedin: morvalquist
• I'm also including a photo image I would like to use. The photo's background is not needed, and to be honest isn't really desireable. Just looking to use the image of me.
Nice to have
• I'm attaching which could be used as is, omitted from the card, or altered maybe with text going around the outside of the circle or in some other way. It may need some clean up to the edges of the lettering as we only use it for the website thumbnail.
• If there's space I'd like to include the text "join our mailing list for a free song download: freesong.morvalquist.com" If not perhaps just "Download a Free Song at: freesong.morvalquist.com - something to this end.
Should not have
• anything cartoony. Don't think retro 90s's vision of the swing era, think actual swing era!
• anything modern. Got to look old school
• Try to avoid dark backgrounds. Since we often play in bars and clubs where it is dar, a d
• avoid script fonts.

```html
<!DOCTYPE html>
<html lang="en">
<head>
<meta charset="utf-8">
<title>Tobin Vashley — Business Card</title>
<link href="https://fonts.googleapis.com/css2?family=Josefin+Sans:wght@400;600&display=swap" rel="stylesheet">
<style>
  :root {
    --backdrop: #3b3531;
    --paper: #e8dbc0;
    --paper-edge: #d8c6a2;
    --ink: #2a2119;
    --ink-soft: #4a3b2c;
    --rule: #8a7556;
  }
  * { margin: 0; padding: 0; box-sizing: border-box; }
  html, body {
    width: 1200px; height: 900px; overflow: hidden;
    background: var(--backdrop);
    font-family: "Josefin Sans", "Century Gothic", sans-serif;
    color: var(--ink);
  }
  .canvas { position: relative; width: 1200px; height: 900px; }

  .card {
    position: absolute;
    top: 295px;
    width: 540px; height: 309px;
    background: radial-gradient(ellipse at 50% 45%, var(--paper) 55%, var(--paper-edge) 100%);
    box-shadow: 0 10px 28px rgba(0,0,0,0.45);
  }
  .card--front { left: 40px; }
  .card--back { left: 620px; }

  .card__frame {
    position: absolute; inset: 12px;
    border: 1px solid var(--rule);
    pointer-events: none;
  }
  .card__frame::after {
    content: ""; position: absolute; inset: 4px;
    border: 2px solid var(--rule);
  }

  .wordmark {
    position: absolute;
    display: flex; align-items: center; gap: 10px;
    font-weight: 600;
    font-size: 26px;
    letter-spacing: 2px;
    text-transform: uppercase;
    color: var(--ink);
  }
  .wordmark__dot {
    width: 12px; height: 12px; border-radius: 50%;
    background: var(--ink);
  }
  .card--front .wordmark { left: 140px; top: 72px; }
  .card--back .wordmark { left: 44px; top: 128px; }

  .holder-name {
    position: absolute; left: 42px; top: 228px;
    font-size: 23px; font-weight: 600;
    letter-spacing: 1px;
  }
  .divider {
    position: absolute; left: 268px; top: 190px;
    width: 1px; height: 90px;
    background: var(--rule);
  }
  .contact-list {
    position: absolute; left: 286px; top: 196px;
    list-style: none;
    font-size: 14px; line-height: 24px;
    color: var(--ink-soft);
  }
  .contact-list li { display: flex; align-items: center; gap: 9px; }
  .contact-list svg { width: 11px; height: 11px; fill: var(--ink); flex: none; }

  .social-list {
    position: absolute; left: 318px; top: 44px;
    list-style: none;
    font-size: 13px; line-height: 22px;
    color: var(--ink-soft);
  }
  .social-list li { display: flex; align-items: center; gap: 9px; }
  .social-list__mark { width: 9px; height: 9px; background: var(--ink); flex: none; }

  .roles {
    position: absolute; right: 40px; top: 236px;
    font-size: 15px; letter-spacing: 0.5px;
    color: var(--ink);
  }
</style>
</head>
<body>
<main class="canvas">

  <section class="card card--front" aria-label="Card front">
    <div class="card__frame"></div>
    <div class="wordmark"><span class="wordmark__dot"></span>Morvalquist</div>
    <div class="holder-name">Tobin Vashley</div>
    <div class="divider"></div>
    <ul class="contact-list">
      <li>
        <svg viewBox="0 0 24 24" aria-hidden="true"><path d="M6.6 10.8a15.1 15.1 0 0 0 6.6 6.6l2.2-2.2c.3-.3.7-.4 1-.2 1.1.4 2.3.6 3.6.6.6 0 1 .4 1 1V20c0 .6-.4 1-1 1C10.6 21 3 13.4 3 4c0-.6.4-1 1-1h3.5c.6 0 1 .4 1 1 0 1.3.2 2.5.6 3.6.1.3 0 .7-.2 1z"/></svg>
        646-555-0148
      </li>
      <li>
        <svg viewBox="0 0 24 24" aria-hidden="true"><path d="M2 5h20v14H2z M3.5 6.5 12 13l8.5-6.5z" fill-rule="evenodd"/></svg>
        tobin@morvalquist.com
      </li>
      <li>
        <svg viewBox="0 0 24 24" aria-hidden="true"><circle cx="12" cy="12" r="10"/></svg>
        morvalquist.com
      </li>
    </ul>
  </section>

  <section class="card card--back" aria-label="Card back">
    <div class="card__frame"></div>
    <div class="wordmark"><span class="wordmark__dot"></span>Morvalquist</div>
    <ul class="social-list">
      <li><span class="social-list__mark"></span>morvalquist.com</li>
      <li><span class="social-list__mark"></span>@morvalquist</li>
      <li><span class="social-list__mark"></span>@morvalquist</li>
      <li><span class="social-list__mark"></span>morvalquist</li>
    </ul>
    <p class="roles">Bandleader, Guitarist, Vocalist, Songwriter</p>
  </section>

</main>
</body>
</html>
```